Proposal for a new Label - Proposal for a new Label

New design for label, renewal of existing label for more than 10 years, we want to change the image of the label, highlighting the name QTM-R3 and giving more notoriety to the brand, keeping the rest of the information on the label, changing the location , color tone and tone, you can vary the tone of the colors, a stronger or softer orange, a darker or lighter gray, the corporate colors recognized by customers are white, orange and gray. The product is a powder additive that is used in the extraction of copper, the base is a bag of Kraf paper of 25 Kg. This product has been awarded as an innovative product, which marked a precedent in the mining industry positively impacting the quality of the copper produced. New design for label, renew existing label for more than 10 years, we want to change the image of the label, highlighting the name QTM-R3 and giving more notoriety to the brand, keeping the rest of the information on the label, changing location , font. and hue of colors, being able to be a stronger orange or a darker gray or vice versa, the corporate colors recognized by the clients are white, orange and gray. The product is a powder additive that is used in copper mining, the base is a bag of Kraf paper of 25 Kg. This product has been awarded as an innovative product, which is marked in the mining industry impacting the quality of copper produced.

Target Market(s)

Mining - Mining

Colors
f04a50
ec1f27
f59296
f68e4d
f37122
f8ba93
757575
cfcfcf
c4c4c4

Requirements
Must have
• 217mm X 330mm Highlight the brand Highlight the brand
Nice to have
• At the base of the label place the flags of the mining countries where the additive is used: Chile, Peru, Mexico, Spain, DR Congo, Zambia, Laos, Kazakhstan, Australia. At the base of the label, place the flags of the mining countries where the additive is used: Chile, Peru, Mexico, Spain, Congo DRC, Zambia, Laos, Kazakhstan, Australia. Indicate in a corner or place on the label that it is a global product. Indicate in a corner or place on the label that is a global product.

```html
<!DOCTYPE html>
<html lang="en">
<head>
<meta charset="utf-8">
<title>QTM-R3 grain refiner label</title>
<link rel="stylesheet" href="https://fonts.googleapis.com/css2?family=Montserrat:wght@700;800&family=Quicksand:wght@500&family=Arimo:wght@400;700&display=swap">
<style>
  :root{
    --backdrop:#6e4b32;
    --orange-top:#ff5000;
    --orange-mid:#f96b0c;
    --orange-bottom:#f2a300;
    --white:#ffffff;
    --gray-dark:#555555;
    --gray-mid:#757575;
    --red-line:#c8313a;
    --badge-red:#d0333b;
  }
  *{margin:0;padding:0;box-sizing:border-box}
  html,body{width:1200px;height:1000px;overflow:hidden;background:var(--backdrop)}
  .canvas{position:relative;width:1200px;height:1000px;background:var(--backdrop)}
  .label{position:absolute;left:38px;top:120px;width:1122px;height:738px;background:var(--white);font-family:'Arimo',Arial,sans-serif}
  .label__brand-area{position:absolute;left:0;top:0;width:864px;height:738px;
    background:linear-gradient(180deg,var(--orange-top) 0%,var(--orange-mid) 55%,var(--orange-bottom) 100%)}
  .company-name{position:absolute;left:62px;top:62px;display:flex;align-items:center;gap:10px;
    font-family:'Montserrat',sans-serif;font-weight:800;font-size:28px;color:var(--white);letter-spacing:1px}
  .company-name__dot{width:22px;height:22px;border-radius:50%;background:var(--white)}
  .product-name{position:absolute;left:60px;top:175px;font-family:'Montserrat',sans-serif;font-weight:800;
    font-size:172px;line-height:1;color:var(--white);letter-spacing:2px}
  .product-type{position:absolute;left:392px;top:430px;font-family:'Quicksand',sans-serif;font-weight:500;
    font-size:62px;color:var(--white);letter-spacing:1px}
  .manufacturer{position:absolute;left:420px;top:528px;width:310px;text-align:center;
    font-weight:700;font-size:15.5px;line-height:19px;color:var(--gray-dark)}
  .global-icons{position:absolute;left:56px;top:654px;display:flex;gap:26px}
  .flags{position:absolute;left:215px;top:653px;display:flex;gap:2px}
  .flag{width:64px;height:42px}
  .info-panel{position:absolute;left:864px;top:0;width:258px;height:738px;color:#333}
  .field{position:absolute;left:0;width:243px}
  .field__label{font-weight:700;font-size:10px;color:#333;margin-left:18px;margin-bottom:4px}
  .field__box{height:31px;border:1px solid var(--gray-mid);border-left:none;border-radius:0 9px 9px 0;background:var(--white)}
  .divider{position:absolute;left:-20px;width:251px;height:2px;background:var(--red-line)}
  .safety{position:absolute;left:0;top:228px;width:256px;text-align:center;font-size:10.5px;line-height:12.5px}
  .safety h3{font-size:10.5px;font-weight:700;margin-bottom:4px}
  .safety h3.first-aid{margin-top:10px}
  .handling{position:absolute;left:0;top:440px;width:256px;text-align:center}
  .handling__icons{display:flex;justify-content:center;gap:14px;margin-bottom:14px}
  .handling__note{font-size:9px;line-height:11px}
  .weight{position:absolute;left:0;top:532px;width:256px;text-align:center;color:var(--gray-dark);font-weight:700}
  .weight__label{font-size:14px}
  .weight__value{font-size:30px;margin-top:4px}
  .award-badge{position:absolute;left:70px;top:630px}
</style>
</head>
<body>
<div class="canvas">
  <div class="label">
    <section class="label__brand-area">
      <div class="company-name"><span class="company-name__dot"></span>K-METALIX</div>
      <h1 class="product-name">QTM-R3</h1>
      <p class="product-type">grain refiner</p>
      <address class="manufacturer" style="font-style:normal">
        SOCIEDAD NORTE ALEA LTDA.<br>
        Calle Los Cobres, 215 Galpón 14<br>
        Barrio Industrial, Copiapó<br>
        COPIAPÓ, CHILE<br>
        Fono: 56-52-2000141 / 56-52-2000142
      </address>
      <div class="global-icons">
        <svg width="52" height="44" viewBox="0 0 52 44" aria-label="Mining">
          <g stroke="#fff" stroke-width="4" stroke-linecap="round" fill="none">
            <line x1="8" y1="40" x2="42" y2="8"/><line x1="44" y1="40" x2="10" y2="8"/>
            <path d="M2 12 Q14 0 26 6"/><path d="M50 12 Q38 0 26 6"/>
          </g>
        </svg>
        <svg width="48" height="48" viewBox="0 0 48 48" aria-label="Global product">
          <g stroke="#fff" stroke-width="2.5" fill="none">
            <circle cx="24" cy="24" r="21"/><ellipse cx="24" cy="24" rx="9" ry="21"/>
            <line x1="3" y1="24" x2="45" y2="24"/><path d="M7 13 H41 M7 35 H41"/>
          </g>
        </svg>
      </div>
      <div class="flags">
        <div class="flag" role="img" aria-label="Flag of Chile" style="background:linear-gradient(180deg,#fff 50%,#d52b1e 50%)"></div>
        <div class="flag" role="img" aria-label="Flag of Peru" style="background:linear-gradient(90deg,#d91023 33%,#fff 33%,#fff 67%,#d91023 67%)"></div>
        <div class="flag" role="img" aria-label="Flag of Laos" style="background:linear-gradient(180deg,#ce1126 25%,#002868 25%,#002868 75%,#ce1126 75%)"></div>
        <div class="flag" role="img" aria-label="Flag of Mexico" style="background:linear-gradient(90deg,#006847 33%,#fff 33%,#fff 67%,#ce1126 67%)"></div>
        <div class="flag" role="img" aria-label="Flag of Spain" style="background:linear-gradient(180deg,#c60b1e 25%,#ffc400 25%,#ffc400 75%,#c60b1e 75%)"></div>
        <div class="flag" role="img" aria-label="Flag of Zambia" style="background:#198a00"></div>
        <div class="flag" role="img" aria-label="Flag of Kazakhstan" style="background:#00afca"></div>
        <div class="flag" role="img" aria-label="Flag of the Congo" style="background:linear-gradient(135deg,#009543 40%,#fbde4a 40%,#fbde4a 60%,#dc241f 60%)"></div>
        <div class="flag" role="img" aria-label="Flag of Australia" style="background:#012169"></div>
      </div>
    </section>

    <aside class="info-panel">
      <div class="field" style="top:26px"><p class="field__label">LOT NUMBER:</p><div class="field__box"></div></div>
      <div class="field" style="top:86px"><p class="field__label">DATE OF MANUFACTURE:</p><div class="field__box"></div></div>
      <div class="field" style="top:145px"><p class="field__label">EXPIRATION:</p><div class="field__box"></div></div>
      <div class="divider" style="top:212px"></div>

      <div class="safety">
        <h3>SAFETY INFORMATION</h3>
        <p>-Avoid contact with skin<br>-Avoid breathing dust<br>-Use proper protection<br>-Store in cool &nbsp;and ventilated<br>-Spills: Pick up with absorbent material<br>-Fire: extinguishers should use dry<br>chemical, CO2, foam or water</p>
        <h3 class="first-aid">FIRST AIDS</h3>
        <p>*Eye contact: wash with abundant water<br>at least for 15 minutes<br>*Scin contact: Wash with soap and water.</p>
      </div>
      <div class="divider" style="top:419px"></div>

      <div class="handling">
        <div class="handling__icons">
          <svg width="34" height="30" viewBox="0 0 34 30" aria-label="Keep dry"><path d="M3 14 Q17 0 31 14 Z" fill="#444"/><path d="M17 14 V25 Q17 28 14 27" stroke="#444" stroke-width="2" fill="none"/></svg>
          <svg width="36" height="30" viewBox="0 0 36 30" aria-label="Store under cover"><path d="M2 12 L18 2 L34 12" stroke="#444" stroke-width="3" fill="none"/><rect x="6" y="16" width="24" height="4" fill="#444"/><rect x="6" y="24" width="24" height="4" fill="#444"/></svg>
          <svg width="30" height="30" viewBox="0 0 30 30" aria-label="Keep away from sunlight"><circle cx="14" cy="15" r="7" fill="none" stroke="#444" stroke-width="2"/><rect x="22" y="1" width="5" height="28" fill="#444"/></svg>
        </div>
        <p class="handling__note">Product not classified as dangerous,<br>according to the legislation transport.</p>
      </div>

      <div class="weight"><p class="weight__label">NET WEIGHT:</p><p class="weight__value">25 Kg</p></div>
      <div class="divider" style="top:601px"></div>

      <svg class="award-badge" width="120" height="68" viewBox="0 0 120 68" role="img" aria-label="Innovation award badge">
        <ellipse cx="60" cy="34" rx="58" ry="32" fill="var(--badge-red)"/>
        <ellipse cx="60" cy="34" rx="46" ry="20" fill="#fff"/>
      </svg>
    </aside>
  </div>
</div>
</body>
</html>
```